I need a business card design for a new business based in South West Australia.
I specialize in residential window cleaning & general handyman maintenance.

Dale Marsh - 412 SILVER HAWK DETAILING
- Window Cleaning
- House Maintenance

```html
<!DOCTYPE html>
<html lang="en">
<head>
<meta charset="utf-8">
<title>412 Silver Hawk Detailing – Business Card</title>
<link rel="stylesheet" href="https://fonts.googleapis.com/css2?family=Old+Standard+TT:wght@400;700&display=swap">
<style>
  :root {
    --page-bg: #d9d4cc;
    --card-maroon: #2c1013;
    --sky-light: #c9d8ee;
    --sky-mid: #a9bfe0;
    --sky-deep: #95acd3;
    --band-white: #ffffff;
    --band-black: #0c0c0c;
    --ink-dark: #141414;
    --ink-light: #ffffff;
  }
  html, body {
    margin: 0;
    padding: 0;
    width: 1200px;
    height: 902px;
    overflow: hidden;
    background: var(--page-bg);
  }
  .stage {
    position: relative;
    width: 1200px;
    height: 902px;
  }
  .business-card {
    position: absolute;
    left: 110px;
    top: 166px;
    width: 980px;
    height: 570px;
    box-shadow: 0 18px 40px rgba(0,0,0,0.35);
  }
  .business-card svg { display: block; }
  .company-name {
    font-family: "Old Standard TT", serif;
    font-weight: 700;
    font-size: 46px;
    fill: var(--ink-dark);
    letter-spacing: 0.5px;
  }
  .service-line {
    font-family: "Old Standard TT", serif;
    font-weight: 700;
    font-size: 27px;
    fill: var(--ink-dark);
  }
  .person-name {
    font-family: "Old Standard TT", serif;
    font-weight: 400;
    font-size: 54px;
    fill: var(--ink-light);
  }
  .person-role {
    font-family: "Old Standard TT", serif;
    font-weight: 400;
    font-size: 28px;
    fill: var(--ink-light);
  }
</style>
</head>
<body>
<main class="stage">
  <div class="business-card">
    <svg width="980" height="570" viewBox="0 0 980 570" xmlns="http://www.w3.org/2000/svg">
      <defs>
        <linearGradient id="window-tones" x1="0" y1="0" x2="1" y2="0.4">
          <stop offset="0" stop-color="var(--sky-light)"/>
          <stop offset="0.55" stop-color="var(--sky-mid)"/>
          <stop offset="1" stop-color="var(--sky-deep)"/>
        </linearGradient>
      </defs>

      <!-- card base -->
      <rect class="card-base" x="0" y="0" width="980" height="570" fill="var(--card-maroon)"/>

      <!-- upper photo area -->
      <path class="window-photo" role="img" aria-label="Photo of a soapy window pane being wiped with a squeegee"
            d="M0 0 H980 V200 L200 318 L0 312 Z" fill="url(#window-tones)"/>

      <!-- chevron divider bands -->
      <path class="divider-white" d="M0 312 L200 318 L980 200 V222 L210 342 L0 336 Z" fill="var(--band-white)"/>
      <path class="divider-black" d="M0 336 L210 342 L980 222 V232 L214 356 L0 350 Z" fill="var(--band-black)" opacity="0.9"/>

      <!-- company heading -->
      <text class="company-name" x="150" y="130">412 SILVER HAWK DETAILING</text>
      <text class="service-line" x="290" y="184">residential window cleaning &amp;</text>
      <text class="service-line" x="300" y="224">general handyman maintenance</text>

      <!-- personal details -->
      <text class="person-name" x="600" y="430" text-anchor="middle">Dale Marsh</text>
      <text class="person-role" x="600" y="486" text-anchor="middle">House Maintenance</text>
      <text class="person-role" x="600" y="526" text-anchor="middle">Window Cleaning</text>
    </svg>
  </div>
</main>
</body>
</html>
```